4D Cradle Glimpse Luxury Ultrasound Billboard

Design a HIGH-END, MODERN billboard for my private prenatal ultrasound studio, 4D Cradle Glimpse, located in Pace, Florida.
This billboard will be viewed by drivers traveling at highway speeds, so it must be extremely clean, simple, and readable within 6 seconds.
About My Business
4D Cradle Glimpse is a private prenatal ultrasound studio specializing in:
Highest technology 4D/HD Ultrasounds
Early Gender Determination
Pregnancy Confirmation
I have been serving families for nearly 10 years and is known for creating a memorable experience, not just an ultrasound appointment.
Design Style
I DO NOT want:
Flowers
Leaves
Swirls
Glitter
Hearts everywhere
Busy backgrounds
Generic maternity stock graphics
I DO want:
Modern
Luxury
Upscale
Clean
Professional
Eye-catching
Premium medical spa feel
Colors
Use colors from my logo:
LOGO Green ( or a deep green)
Black
White
Soft Gold accents
Images:
Incorporate my professional headshot in a clean, modern way, logo, and the ultrasound images
Text
Keep wording minimal.
Primary Headline ( OPEN TO IDEAS) :
EXAMPLES ( WOULD RATHER SOMETHING MORE CATCHY)
" ADVANCED IMAGING. UNFORGETTABLE MOMENTS"
"MEET YOUR BABY BEFORE BIRTH"
Under headline:
4D Ultrasound • Early Gender • Pregnancy Confirmation
Business Name:
4D Cradle Glimpse
Private Prenatal Ultrasound Studio
Phone Number:
850-471-5923
Important
This billboard must be readable in 5–6 seconds from a moving vehicle.
Less text is better.
The phone number and business name must be visible from a distance.
The design should feel like a premium brand that immediately tells expecting parents:
“This is where I go to see my baby.”
Files Provided
Official logo
Headshot
Ultrasound images
Don’t make this look like a medical office billboard.
Make it look like a luxury baby experience billboard. That’s what separates 4D Cradle Glimpse from hospitals, OB offices, and all the new studios popping up around you. The emotional connection is what gets moms to book. ❤️
Billboard Size - 10.6” x 36”

```html
<!DOCTYPE html>
<html lang="en">
<head>
<meta charset="utf-8">
<title>4D Cradle Glimpse Billboard</title>
<link rel="stylesheet" href="https://fonts.googleapis.com/css2?family=Montserrat:wght@600;700&family=Playfair+Display:wght@500&family=Open+Sans:wght@600&family=Krona+One&display=swap">
<style>
  :root{
    --page:#7a818a;
    --cream:#f6f1e7;
    --paper:#f2f1ef;
    --sage:#5b675e;
    --ink:#4d5951;
    --gold:#b8953f;
    --white:#ffffff;
    --photo-dark:#2a1712;
    --photo-warm:#9a6148;
  }
  html,body{margin:0;padding:0;width:1145px;height:1200px;overflow:hidden;background:var(--page);}
  .billboard{position:absolute;left:30px;top:421px;width:1085px;height:357px;overflow:hidden;background:var(--cream);}
  .billboard-shapes{position:absolute;inset:0;}
  .brand-box{position:absolute;left:20px;top:13px;width:215px;height:106px;box-sizing:border-box;
    border:1.5px solid var(--sage);border-radius:10px;background:var(--white);
    display:flex;flex-direction:column;align-items:center;justify-content:center;}
  .brand-name{font-family:"Montserrat",sans-serif;font-weight:700;font-size:19px;color:var(--gold);letter-spacing:.2px;}
  .brand-rule{width:180px;height:1px;background:var(--gold);margin:10px 0 8px;}
  .brand-tagline{font-family:"Montserrat",sans-serif;font-weight:600;font-size:8.5px;color:var(--ink);letter-spacing:.3px;}
  .headshot{position:absolute;left:30px;top:124px;width:175px;height:233px;
    background:linear-gradient(180deg,#e2cba3 0%,#cfb283 38%,#3f4b40 62%,#3a463b 80%,#e6e6e6 100%);}
  .headline{position:absolute;left:316px;top:0;width:500px;height:240px;margin:0;color:var(--ink);font-weight:normal;}
  .headline-line{position:absolute;left:0;width:100%;text-align:center;white-space:nowrap;}
  .headline-top{top:15px;font-family:"Montserrat",sans-serif;font-weight:700;font-size:56px;line-height:1;letter-spacing:1px;}
  .headline-main{top:52px;font-family:"Playfair Display",serif;font-weight:500;font-size:140px;line-height:1;color:var(--gold);letter-spacing:8px;}
  .headline-bottom{top:184px;font-family:"Montserrat",sans-serif;font-weight:700;font-size:52px;line-height:1;letter-spacing:1px;}
  .services{position:absolute;left:303px;top:244px;width:502px;height:31px;box-sizing:border-box;
    background:var(--sage);border:1.5px solid var(--gold);border-radius:15px;
    display:flex;align-items:center;justify-content:center;gap:9px;
    font-family:"Open Sans",sans-serif;font-weight:600;font-size:15.5px;color:var(--white);white-space:nowrap;}
  .services .dot{width:5px;height:5px;border-radius:50%;background:var(--gold);}
  .phone{position:absolute;left:400px;top:299px;display:flex;align-items:center;gap:17px;}
  .phone-icon{width:39px;height:39px;border-radius:50%;background:var(--gold);display:flex;align-items:center;justify-content:center;}
  .phone-number{font-family:"Krona One",sans-serif;font-size:46px;line-height:1;color:var(--white);letter-spacing:2px;white-space:nowrap;}
</style>
</head>
<body>
<main class="billboard">
  <svg class="billboard-shapes" width="1085" height="357" viewBox="0 0 1085 357">
    <defs>
      <radialGradient id="ultrasound-tone" cx="60%" cy="45%" r="70%">
        <stop offset="0" stop-color="var(--photo-warm)"/>
        <stop offset=".6" stop-color="#6e3f2f"/>
        <stop offset="1" stop-color="var(--photo-dark)"/>
      </radialGradient>
    </defs>
    <rect width="1085" height="357" fill="var(--cream)"/>
    <path class="side-panel" d="M0,0 H313 Q290,190 208,357 H0 Z" fill="var(--paper)"/>
    <path class="side-divider" d="M313,0 Q290,190 208,357" fill="none" stroke="var(--gold)" stroke-width="3"/>
    <path class="bottom-band" d="M262,283 H1085 V357 H208 Z" fill="var(--sage)"/>
    <line x1="262" y1="283" x2="1085" y2="283" stroke="var(--gold)" stroke-width="2"/>
    <path class="photo-frame" d="M780,0 C822,90 842,200 822,283 H1085 V0 Z" fill="var(--sage)"/>
    <path class="ultrasound-photo" role="img" aria-label="4D ultrasound image of twin babies facing each other"
      d="M796,0 C838,90 858,200 838,283 H1085 V0 Z" fill="url(#ultrasound-tone)" stroke="var(--gold)" stroke-width="1.5"/>
  </svg>

  <div class="brand-box">
    <div class="brand-name">4D Cradle Glimpse</div>
    <div class="brand-rule"></div>
    <div class="brand-tagline">PRENATAL ULTRASOUND STUDIO</div>
  </div>

  <div class="headshot" role="img" aria-label="Headshot of the studio owner in dark green scrubs"></div>

  <h1 class="headline">
    <span class="headline-line headline-top">MEET YOUR</span>
    <span class="headline-line headline-main">BABY</span>
    <span class="headline-line headline-bottom">BEFORE BIRTH</span>
  </h1>

  <div class="services">
    <span>4D Ultrasound</span><span class="dot"></span>
    <span>Early Gender</span><span class="dot"></span>
    <span>Pregnancy Confirmation</span>
  </div>

  <div class="phone">
    <div class="phone-icon">
      <svg width="22" height="22" viewBox="0 0 24 24" aria-hidden="true">
        <path d="M6.6 10.8c1.4 2.8 3.8 5.1 6.6 6.6l2.2-2.2c.3-.3.7-.4 1-.2 1.1.4 2.3.6 3.6.6.6 0 1 .4 1 1V20c0 .6-.4 1-1 1C10.6 21 3 13.4 3 4c0-.6.4-1 1-1h3.5c.6 0 1 .4 1 1 0 1.3.2 2.5.6 3.6.1.3 0 .7-.2 1L6.6 10.8z" fill="var(--white)"/>
      </svg>
    </div>
    <div class="phone-number">850-471-5923</div>
  </div>
</main>
</body>
</html>
```